Larkspur Talent IT Recruiting firm needs a business card design for Recruiters, Sourcers, and Account

We need business cards that allow us to change all contact info, names, titles (Recruiter, Sourcer, Account Manager, Director, CEO, etc) per person since we have three offices, in three cities, Phoenix, Austin, and Las Vegas. We do recruiting and contractors for IT positions (Developers, Architects, Software Engineers, Security Engineers, Help Desk, DBAs, PMs, Scrum Masters, etc.) Our client companies are very diverse from Meridian 100 to silicone Valley type start-ups.

So, while we what hip, techie, and quirky, it still needs to be professional. Primary color we use is blue, with silver as a secondary color.

Target Market(s)

IT, Technology

Industry/Entity Type

Business

Contact Information for Business Card

Company name: Larkspur Talent, Inc.
Website: www.larkspurtalent.example
Logos for Careerloop, Blipster, and Myriada

Name, Title, Office Number, Cell Number, email

Font styles to use
Serif
Sans Serif

Colors
0455a3
d5d5d5

Requirements
Nice to have
• The grey I selected below is not necessary - but, would like silver included. I included a card design (File 3: LTI early trial example.jpg) that I had started on. It's very rough, and not quite what we're looking for, but what we did like is the logo, big, maybe a bit faded, off center, goes out of frame, etc. Still looking for other ideas - you are the pros! But, just an idea of a design element we liked.

```html
<!DOCTYPE html>
<html lang="en">
<head>
<meta charset="utf-8">
<title>Larkspur Talent – Business Card</title>
<link rel="stylesheet" href="https://fonts.googleapis.com/css2?family=Cinzel:wght@400;600&family=PT+Sans:wght@400;700&display=swap">
<style>
  :root {
    --brand-blue: #0455a3;
    --silver: #d5d5d5;
    --white: #ffffff;
    --ink: #1f1f1f;
    --stage: #ececec;
  }
  * { margin: 0; padding: 0; box-sizing: border-box; }
  html, body { width: 1200px; height: 1094px; overflow: hidden; }
  body {
    background: var(--stage);
    position: relative;
    font-family: "PT Sans", Arial, sans-serif;
  }
  .card {
    position: absolute;
    width: 841px;
    height: 479px;
    border-radius: 27px;
    overflow: hidden;
    background: var(--brand-blue);
    box-shadow: 0 4px 14px rgba(0,0,0,.18);
  }
  .card--front { left: 51px; top: 50px; }
  .card--back { left: 312px; top: 569px; }

  .front-shapes { position: absolute; inset: 0; }

  .brand-lockup {
    position: absolute;
    left: 34px;
    top: 196px;
    width: 380px;
    display: flex;
    align-items: center;
    gap: 14px;
  }
  .brand-dot {
    width: 42px; height: 42px;
    border-radius: 50%;
    background: var(--brand-blue);
    flex: none;
  }
  .brand-name {
    font-family: "Cinzel", Georgia, serif;
    font-weight: 400;
    font-size: 37px;
    line-height: 1;
    color: var(--ink);
    letter-spacing: 1px;
    white-space: nowrap;
  }
  .tagline {
    position: absolute;
    left: 45px;
    top: 300px;
    width: 331px;
    text-align: center;
    font-family: "Cinzel", Georgia, serif;
    font-size: 17px;
    letter-spacing: 2.4px;
    color: var(--ink);
    white-space: nowrap;
  }

  .contact-block {
    position: absolute;
    right: 38px;
    top: 100px;
    text-align: right;
    color: var(--white);
  }
  .person-name { font-weight: 700; font-size: 28px; line-height: 1.2; }
  .person-title { font-size: 20px; line-height: 1.3; margin-top: 2px; }
  .contact-list { list-style: none; margin-top: 38px; }
  .contact-item {
    font-size: 19px;
    line-height: 33.5px;
    display: flex;
    justify-content: flex-end;
    align-items: center;
    gap: 8px;
  }
  .contact-icon { width: 17px; height: 17px; flex: none; }
  .social-dot {
    width: 18px; height: 18px;
    border-radius: 50%;
    background: var(--white);
    flex: none;
  }

  .faint-mark {
    position: absolute;
    left: 505px;
    top: 110px;
    width: 260px; height: 260px;
    border-radius: 50%;
    background: rgba(255,255,255,.08);
  }

  .back-mark {
    position: absolute;
    left: 263px;
    top: 67px;
    width: 308px; height: 308px;
    border-radius: 50%;
    background: var(--white);
    display: flex;
    align-items: center;
    justify-content: center;
  }
  .back-mark-name {
    font-family: "Cinzel", Georgia, serif;
    font-size: 30px;
    line-height: 1.15;
    color: var(--brand-blue);
    text-align: center;
  }
  .back-url {
    position: absolute;
    left: 0; right: 0;
    top: 400px;
    text-align: center;
    color: var(--white);
    font-size: 25px;
    letter-spacing: 3px;
  }
</style>
</head>
<body>

<section class="card card--front" aria-label="Business card front">
  <svg class="front-shapes" width="841" height="479" viewBox="0 0 841 479" aria-hidden="true">
    <circle cx="252" cy="240" r="242" fill="var(--silver)"/>
    <circle cx="236" cy="240" r="242" fill="var(--white)"/>
  </svg>

  <div class="faint-mark" aria-hidden="true"></div>

  <div class="brand-lockup">
    <span class="brand-dot" aria-hidden="true"></span>
    <span class="brand-name">Larkspur Talent</span>
  </div>
  <p class="tagline">RISING TO THE CHALLENGE</p>

  <div class="contact-block">
    <h1 class="person-name">Maren Holloway</h1>
    <p class="person-title">First Touch Embassador</p>
    <ul class="contact-list">
      <li class="contact-item">
        <svg class="contact-icon" viewBox="0 0 24 24" aria-hidden="true"><path fill="#fff" d="M6.6 10.8a15.1 15.1 0 0 0 6.6 6.6l2.2-2.2c.3-.3.7-.4 1-.2 1.1.4 2.3.6 3.6.6.6 0 1 .4 1 1V20c0 .6-.4 1-1 1A17 17 0 0 1 3 4c0-.6.4-1 1-1h3.5c.6 0 1 .4 1 1 0 1.3.2 2.5.6 3.6.1.3 0 .7-.2 1z"/></svg>
        <span>555-010-4172</span>
      </li>
      <li class="contact-item">
        <svg class="contact-icon" viewBox="0 0 24 24" aria-hidden="true"><path fill="#fff" d="M2 6h20v12H2z"/><path fill="none" stroke="var(--brand-blue)" stroke-width="2" d="M2 6l10 7 10-7"/></svg>
        <span>maren@larkspurtalent.example</span>
      </li>
      <li class="contact-item">
        <svg class="contact-icon" viewBox="0 0 24 24" aria-hidden="true"><g fill="none" stroke="#fff" stroke-width="1.8"><circle cx="12" cy="12" r="9.5"/><ellipse cx="12" cy="12" rx="4.5" ry="9.5"/><path d="M2.5 12h19M4 7h16M4 17h16"/></g></svg>
        <span>www.larkspurtalent.example</span>
      </li>
      <li class="contact-item">
        <span class="social-dot" aria-hidden="true"></span>
        <span>@MarenHollowayLT</span>
      </li>
      <li class="contact-item">
        <span class="social-dot" aria-hidden="true"></span>
        <span>@MarenHollowayLT</span>
      </li>
    </ul>
  </div>
</section>

<section class="card card--back" aria-label="Business card back">
  <div class="back-mark">
    <span class="back-mark-name">Larkspur<br>Talent</span>
  </div>
  <p class="back-url">www.larkspurtalent.example</p>
</section>

</body>
</html>
```